RWT Fittings Ltd Business Cards

We need a business card with our business logo. We provide window and door installations on high-rises in west coast British Colombia, Canada.

I would like my business information and details on one side of the card, and the other side the company name with logo

Target Market(s)

General Contractors

Industry/Entity Type

Construction

Contact Information for Business Card

one side i want my company name and logo in the dark theme logo that i provided

Requirements
Must have
• Marco Peltieri, 16045518293, RWTFittings@mailbox-demo.com, 1407-5194 Linden Row Burnaby BC, V5H 2K9, Owner & Manager

```html
<!DOCTYPE html>
<html lang="en">
<head>
<meta charset="UTF-8">
<title>RWT Fittings Ltd — Business Cards</title>
<link href="https://fonts.googleapis.com/css2?family=Montserrat:wght@600;700;800&family=Roboto:wght@400;500&display=swap" rel="stylesheet">
<style>
  :root {
    --page-bg: #2a2a2d;
    --card-dark: #222226;
    --photo-light: #5d554c;
    --photo-dark: #1d1b19;
    --brand-blue: #29a9e6;
    --brand-blue-light: #3fbbe9;
    --text-white: #f2f2f2;
  }
  * { margin: 0; padding: 0; box-sizing: border-box; }
  html, body {
    width: 1200px;
    height: 780px;
    overflow: hidden;
    background: var(--page-bg);
  }
  .canvas {
    position: relative;
    width: 1200px;
    height: 780px;
    display: flex;
    align-items: center;
    justify-content: center;
    gap: 40px;
  }
  .card {
    position: relative;
    width: 540px;
    height: 309px;
    overflow: hidden;
    border-bottom: 3px solid var(--brand-blue);
    box-shadow: 0 18px 40px rgba(0,0,0,0.45);
  }

  /* Front side */
  .card--front { background: var(--photo-dark); }
  .front-photo {
    position: absolute;
    inset: 0;
    background: linear-gradient(215deg, var(--photo-light) 0%, #3a3530 45%, var(--photo-dark) 100%);
  }
  .front-brand {
    position: absolute;
    inset: 0;
    display: flex;
    align-items: center;
    justify-content: center;
    gap: 14px;
  }
  .brand-mark {
    width: 34px;
    height: 34px;
    background: var(--brand-blue-light);
  }
  .brand-name {
    font-family: 'Montserrat', sans-serif;
    font-weight: 700;
    color: var(--brand-blue-light);
    letter-spacing: 0.5px;
  }
  .front-brand .brand-name { font-size: 36px; }

  /* Back side */
  .card--back { background: var(--card-dark); }
  .accent-bar {
    position: absolute;
    top: 0;
    right: 0;
    width: 12px;
    height: 58px;
    background: var(--brand-blue);
  }
  .holder {
    position: absolute;
    top: 22px;
    right: 30px;
    text-align: right;
  }
  .holder-name {
    font-family: 'Montserrat', sans-serif;
    font-weight: 800;
    font-size: 27px;
    color: var(--brand-blue);
    line-height: 1.1;
  }
  .holder-name .surname { color: var(--text-white); }
  .holder-role {
    font-family: 'Montserrat', sans-serif;
    font-weight: 600;
    font-size: 13px;
    color: var(--text-white);
    margin-top: 3px;
  }
  .back-brand {
    position: absolute;
    left: 34px;
    top: 112px;
    display: flex;
    align-items: center;
    gap: 10px;
  }
  .back-brand .brand-mark { width: 24px; height: 24px; background: var(--brand-blue); }
  .back-brand .brand-name { font-size: 26px; color: var(--brand-blue); }
  .contact {
    position: absolute;
    left: 34px;
    bottom: 24px;
    font-family: 'Roboto', sans-serif;
    font-weight: 400;
    font-size: 14px;
    color: var(--text-white);
    line-height: 1.45;
  }
  .contact-address { margin-bottom: 10px; }
  .contact-line {
    display: flex;
    align-items: center;
    gap: 9px;
  }
  .contact-icon { width: 14px; height: 14px; flex: none; }
</style>
</head>
<body>
<main class="canvas">

  <section class="card card--front" aria-label="Card front">
    <div class="front-photo" role="img" aria-label="Blurred dark photograph of a modern office interior"></div>
    <div class="front-brand">
      <span class="brand-mark"></span>
      <span class="brand-name">RWT Fittings Ltd</span>
    </div>
  </section>

  <section class="card card--back" aria-label="Card back">
    <span class="accent-bar"></span>
    <div class="holder">
      <p class="holder-name">Marco <span class="surname">Peltieri</span></p>
      <p class="holder-role">Owner &amp; Manager</p>
    </div>

    <div class="back-brand">
      <span class="brand-mark"></span>
      <span class="brand-name">RWT Fittings Ltd</span>
    </div>

    <div class="contact">
      <p class="contact-address">1407-5194 Linden Row<br>Burnaby BC, V5H 2K9</p>
      <p class="contact-line">
        <svg class="contact-icon" viewBox="0 0 24 24" aria-hidden="true">
          <path fill="#29a9e6" d="M6.6 10.8a15.1 15.1 0 0 0 6.6 6.6l2.2-2.2a1 1 0 0 1 1-.25 11.4 11.4 0 0 0 3.6.57 1 1 0 0 1 1 1V20a1 1 0 0 1-1 1A17 17 0 0 1 3 4a1 1 0 0 1 1-1h3.5a1 1 0 0 1 1 1c0 1.25.2 2.45.57 3.57a1 1 0 0 1-.25 1z"/>
        </svg>
        <span>1604 551 8293</span>
      </p>
      <p class="contact-line">
        <svg class="contact-icon" viewBox="0 0 24 24" aria-hidden="true">
          <rect x="2" y="5" width="20" height="14" rx="1.5" fill="none" stroke="#29a9e6" stroke-width="2"/>
          <path d="M3 6l9 7 9-7" fill="none" stroke="#29a9e6" stroke-width="2"/>
        </svg>
        <span>RWTFittings@mailbox-demo.com</span>
      </p>
    </div>
  </section>

</main>
</body>
</html>
```